Marwick Jewelers New Website Design

This project is to provide a new design for an existing website. The existing website is marwickjewelers dot com . I have created a overview document that outlines all the details for the project. I do not need the design to be converted into HTML. I have a team for that already so please don't ask. I have a lot of images .. too many to upload here so they are on my dev server located at quillfoxstudio com slash marwick slash assets

Number of Pages Required

1 page

```html
<!DOCTYPE html>
<html lang="en">
<head>
<meta charset="utf-8">
<title>Marwick Jewelers</title>
<link href="https://fonts.googleapis.com/css2?family=Great+Vibes&family=Roboto:wght@400;500;700&display=swap" rel="stylesheet">
<style>
:root{
  --navy:#1e2f5e;
  --navy-dark:#172650;
  --teal:#3f7d87;
  --teal-panel:#4a8b93;
  --ink:#1f2b4d;
  --grey:#5c6170;
  --sky:#e4ecf8;
  --line:#d6dbe4;
  --white:#ffffff;
}
*{box-sizing:border-box;margin:0;padding:0}
html,body{width:1200px;height:4612px;overflow:hidden}
body{position:relative;font-family:'Roboto',sans-serif;color:var(--ink);background:var(--white)}
.abs{position:absolute}
.script{font-family:'Great Vibes',cursive;font-weight:400;color:var(--navy)}
.media{position:absolute;overflow:hidden}

/* header */
.site-header{position:absolute;left:0;top:0;width:1200px;height:133px;background:var(--white);z-index:3}
.brand{position:absolute;display:flex;align-items:center;gap:10px;font-family:'Roboto',sans-serif;font-weight:500;color:var(--navy)}
.brand-dot{width:20px;height:20px;border-radius:50%;background:var(--teal)}
.contact-chip{position:absolute;top:26px;display:flex;align-items:center;gap:10px}
.chip-icon{width:32px;height:32px;border-radius:50%;background:var(--teal);display:flex;align-items:center;justify-content:center}
.chip-label{font-size:12px;color:var(--grey)}
.chip-value{font-size:15px;font-weight:700;color:var(--ink)}
.header-rule{position:absolute;left:107px;width:986px;top:86px;height:1px;background:var(--line)}
.main-nav{position:absolute;left:107px;width:986px;top:100px;display:flex;justify-content:space-between;font-size:14px;font-weight:500;color:var(--ink)}

/* hero */
.hero{position:absolute;left:0;top:133px;width:1200px;height:547px;background:linear-gradient(110deg,#ffffff 45%,#eef2f8 100%)}
.hero-title{position:absolute;left:618px;top:300px;font-size:58px;line-height:1}
.hero-text{position:absolute;left:618px;top:396px;width:470px;font-size:16px;line-height:29px;color:var(--ink)}
.btn-primary{position:absolute;left:620px;top:480px;width:190px;height:47px;border-radius:24px;background:var(--teal);color:var(--white);font-size:15px;font-weight:500;display:flex;align-items:center;justify-content:center;gap:8px}
.slide-nav{position:absolute;left:618px;top:572px;display:flex;gap:22px;font-size:13px;font-weight:500;color:var(--navy)}

/* about */
.about{position:absolute;left:0;top:680px;width:1200px;height:790px;background:var(--sky)}
.circle{position:absolute;border-radius:50%}
.about-title{position:absolute;left:0;width:1200px;top:1140px;text-align:center;font-size:62px}
.about-text{position:absolute;left:143px;width:914px;top:1232px;text-align:center;font-size:13.5px;line-height:27.6px;color:var(--grey)}

/* categories */
.cat-card{position:absolute;background:var(--white);border:1px solid #c9cfd9;padding:9px}
.cat-card .media{position:static;width:100%;height:100%;position:relative}
.cat-label{position:absolute;left:30px;bottom:16px;color:var(--white);font-size:21px;font-weight:700}
.plus{position:absolute;width:62px;height:62px;border-radius:50%;border:2px dotted var(--teal);display:flex;align-items:center;justify-content:center;background:var(--white)}
.plus span{width:52px;height:52px;border-radius:50%;background:var(--teal);color:var(--white);font-size:30px;font-weight:300;display:flex;align-items:center;justify-content:center}

/* section heading */
.section-title{position:absolute;left:0;width:1200px;text-align:center;font-size:58px;line-height:1}
.title-rule{position:absolute;left:575px;width:50px;height:3px;background:var(--teal)}

/* products */
.product-card{position:absolute;top:2164px;width:229px;height:283px;background:var(--white);box-shadow:0 2px 12px rgba(30,47,94,.15);text-align:center}
.product-card .media{left:30px;top:18px;width:169px;height:150px;border-radius:6px}
.product-name{position:absolute;left:0;width:100%;top:202px;font-size:18px;font-weight:700;color:var(--ink)}
.product-desc{position:absolute;left:0;width:100%;top:232px;font-size:14px;color:var(--grey)}

/* video */
.video-band{position:absolute;left:0;top:2552px;width:1200px;height:353px;background:var(--navy)}
.video-frame{position:absolute;left:229px;top:2701px;width:742px;height:385px;border-radius:8px;overflow:hidden;box-shadow:0 8px 24px rgba(0,0,0,.3)}
.play-ring{position:absolute;left:323px;top:144px;width:96px;height:96px;border-radius:50%;border:4px solid var(--white);display:flex;align-items:center;justify-content:center;background:rgba(255,255,255,.15)}
.play-cta{position:absolute;left:416px;top:242px;font-size:34px;font-weight:700;color:var(--white)}
.video-controls{position:absolute;left:36px;right:36px;bottom:12px;height:26px;display:flex;align-items:center;gap:10px}
.video-time{font-size:9px;color:var(--white);background:#000;padding:1px 3px}
.video-track{flex:1;height:5px;background:rgba(255,255,255,.35)}

/* testimonials */
.quote-mark{position:absolute;width:90px;height:70px}
.quote-text{position:absolute;width:280px;text-align:center;font-size:14px;line-height:25px;color:var(--grey)}
.quote-name{position:absolute;width:280px;text-align:center;font-size:16px;font-weight:700;color:var(--ink)}

/* contact */
.contact-band{position:absolute;left:0;top:4026px;width:1200px;height:586px;background:var(--navy)}
.panel{position:absolute;background:var(--teal-panel);color:var(--white)}
.panel h2{font-size:28px;font-weight:700}
.info-row{position:absolute;left:30px;display:flex;align-items:center;gap:14px;font-size:14px}
.hours-row{position:absolute;left:30px;width:280px;display:flex;font-size:13px;padding-bottom:14px;border-bottom:1px solid rgba(255,255,255,.35)}
.hours-row span:first-child{width:150px}
.toggle{position:absolute;width:32px;height:16px;border-radius:8px;background:var(--navy-dark)}
.toggle::after{content:"";position:absolute;left:3px;top:3px;width:10px;height:10px;border-radius:50%;background:var(--white)}
.field{position:absolute;left:36px;width:247px;height:39px;border-radius:20px;background:var(--white);color:#8b909c;font-size:12px;padding:0 18px;display:flex;align-items:center;justify-content:space-between}
.field.area{height:95px;border-radius:14px;align-items:flex-start;padding-top:14px}
.btn-submit{position:absolute;left:36px;top:436px;width:247px;height:36px;border-radius:18px;background:var(--navy);color:var(--white);font-size:14px;font-weight:700;display:flex;align-items:center;justify-content:center}

/* footer */
.footer-nav{position:absolute;left:0;width:1200px;top:4454px;display:flex;justify-content:center;gap:21px;font-size:13px;color:var(--white)}
.socials{position:absolute;left:540px;top:4518px;display:flex;gap:12px}
.socials span{width:32px;height:32px;border-radius:50%;border:1.5px solid var(--white)}
.copyright{position:absolute;left:0;width:1200px;top:4588px;text-align:center;font-size:13px;color:var(--white)}
</style>
</head>
<body>

<header class="site-header">
  <div class="brand" style="left:110px;top:32px;font-size:30px"><span class="brand-dot"></span>Marwick</div>

  <div class="contact-chip" style="left:460px">
    <div class="chip-icon"><svg width="16" height="16" viewBox="0 0 24 24" fill="#fff"><path d="M6.6 10.8a15 15 0 0 0 6.6 6.6l2.2-2.2a1 1 0 0 1 1-.25 11.4 11.4 0 0 0 3.6.57 1 1 0 0 1 1 1V20a1 1 0 0 1-1 1A17 17 0 0 1 3 4a1 1 0 0 1 1-1h3.5a1 1 0 0 1 1 1c0 1.25.2 2.45.57 3.57a1 1 0 0 1-.25 1z"/></svg></div>
    <div><div class="chip-label">Phone</div><div class="chip-value">555-201-4830</div></div>
  </div>
  <div class="contact-chip" style="left:655px">
    <div class="chip-icon"><svg width="16" height="16" viewBox="0 0 24 24" fill="#fff"><path d="M6.6 10.8a15 15 0 0 0 6.6 6.6l2.2-2.2a1 1 0 0 1 1-.25 11.4 11.4 0 0 0 3.6.57 1 1 0 0 1 1 1V20a1 1 0 0 1-1 1A17 17 0 0 1 3 4a1 1 0 0 1 1-1h3.5a1 1 0 0 1 1 1c0 1.25.2 2.45.57 3.57a1 1 0 0 1-.25 1z"/></svg></div>
    <div><div class="chip-label">Toll Free</div><div class="chip-value">888-555-0147</div></div>
  </div>
  <div class="contact-chip" style="left:845px">
    <div class="chip-icon"><svg width="14" height="18" viewBox="0 0 24 30" fill="#fff"><path d="M12 0a11 11 0 0 0-11 11c0 8 11 19 11 19s11-11 11-19A11 11 0 0 0 12 0zm0 15a4 4 0 1 1 0-8 4 4 0 0 1 0 8z"/></svg></div>
    <div><div class="chip-label">Address</div><div class="chip-value" style="font-size:13px">48 Elm St N, Ashford, MN</div></div>
  </div>

  <div class="header-rule"></div>
  <nav class="main-nav">
    <span>Company</span><span>Custom Jewelery Services</span><span>Jewelery Repair Services</span><span>Resources</span><span>Showcase</span><span>Gallery</span><span>Engraving &amp; Trophies</span><span>Gift Ideas</span>
  </nav>
</header>

<section class="hero" aria-label="Hero">
</section>
<section class="about" aria-label="About"></section>

<svg class="abs" style="left:111px;top:183px;z-index:2" width="570" height="540" viewBox="0 0 570 540">
  <path d="M564 78 V3 H3 V537 H564 V458" fill="none" stroke="var(--navy)" stroke-width="6"/>
</svg>
<div class="media" role="img" aria-label="Gold and white gold layered ring with square diamond settings" style="left:170px;top:275px;width:390px;height:330px;border-radius:40%;background:radial-gradient(ellipse at center,#d8a46a 0%,#c9925d 35%,#e9d8c6 65%,#ffffff 80%)"></div>

<h1 class="hero-title script">Say It with a Stone</h1>
<p class="hero-text">From “will you?” to “I do” and every momentous occasion in between, Marwick Jewelers offers a radiant</p>
<div class="btn-primary">CONTACT US
  <svg width="14" height="14" viewBox="0 0 16 16"><circle cx="8" cy="8" r="8" fill="#fff"/><path d="M6.5 4.5 10 8l-3.5 3.5" stroke="var(--teal)" stroke-width="2" fill="none"/></svg>
</div>
<div class="slide-nav">
  <span><svg width="18" height="10" viewBox="0 0 18 10"><path d="M17 5H2M6 1 2 5l4 4" stroke="var(--navy)" stroke-width="1.5" fill="none"/></svg> Prev</span>
  <span>Next <svg width="18" height="10" viewBox="0 0 18 10"><path d="M1 5h15M12 1l4 4-4 4" stroke="var(--navy)" stroke-width="1.5" fill="none"/></svg></span>
</div>

<div class="circle media" role="img" aria-label="Diamond engagement ring resting on dark wood" style="left:215px;top:932px;width:214px;height:214px;background:radial-gradient(circle at 50% 45%,#b8b2ab 0%,#6b4a37 45%,#2a1b14 100%)"></div>
<div class="circle media" role="img" aria-label="Store owners standing together outdoors among autumn trees" style="left:697px;top:932px;width:214px;height:214px;background:radial-gradient(circle at 55% 45%,#3a4560 0%,#1f2637 60%,#121722 100%);left:770px"></div>
<div class="circle media" role="img" aria-label="Owners of the store portrait outdoors" style="left:433px;top:786px;width:334px;height:334px;border:5px solid var(--sky);background:linear-gradient(160deg,#7c8a3f 0%,#a2793f 40%,#3c4a6c 75%,#2b3550 100%)"></div>

<h2 class="about-title script">About Us</h2>
<p class="about-text">Marwick Jewelers is an independent, family owned jewelry store located in the heart of Downtown Ashford. Owner, Daniel Marwick has been with the business since 1990. His wife, Helen, joined the business in 2010, store manager, Tom, came on board in 2016 and Lena joined the team in 2021. Marwick Jewelers specializes in engagement rings, fashion jewelry and custom designed pieces. Whether you want to create the ring of your dreams or re-create a family heirloom, Marwick Jewelers is the place to go. Marwick Jewelers offers on-site repairs and prides themselves on their customer service and competitive prices. Marwick Jewelers offers all the selection of the big stores, but with a small town feel and a no-pressure shopping experience.</p>

<div class="cat-card" style="left:4px;top:1469px;width:381px;height:504px">
  <div class="media" role="img" aria-label="Stacked diamond band rings on a soft grey surface" style="background:radial-gradient(ellipse at 50% 60%,#5a5656 0%,#8d8b8c 40%,#c4c3c4 100%)"><div class="cat-label">Engagement Rings</div></div>
</div>
<div class="plus" style="left:281px;top:1931px"><span>+</span></div>

<div class="cat-card" style="left:408px;top:1469px;width:384px;height:233px">
  <div class="media" role="img" aria-label="Jeweler repairing a diamond ring with tweezers" style="background:linear-gradient(120deg,#1c1d22 0%,#3f3d44 50%,#7a6a5e 100%)"><div class="cat-label">Repair &amp; Services</div></div>
</div>
<div class="plus" style="left:687px;top:1660px"><span>+</span></div>

<div class="cat-card" style="left:408px;top:1741px;width:384px;height:232px">
  <div class="media" role="img" aria-label="Designer sketching jewelry by hand" style="background:linear-gradient(120deg,#8a8581 0%,#6e6965 50%,#4a4643 100%)"><div class="cat-label">Designers</div></div>
</div>
<div class="plus" style="left:687px;top:1931px"><span>+</span></div>

<div class="cat-card" style="left:815px;top:1469px;width:381px;height:504px">
  <div class="media" role="img" aria-label="Model wearing a diamond drop earring and necklace" style="background:linear-gradient(150deg,#6b4a3e 0%,#c99a82 40%,#d8b7a3 70%,#9a7a6a 100%)"><div class="cat-label">Fashion Jewelry</div></div>
</div>
<div class="plus" style="left:1092px;top:1931px"><span>+</span></div>

<h2 class="section-title script" style="top:2052px">Highlight Products</h2>
<div class="title-rule" style="top:2112px"></div>

<div class="product-card" style="left:111px">
  <div class="media" role="img" aria-label="Rose gold multi-band ring with flower diamond centre" style="background:radial-gradient(circle,#d49a86 0%,#f3e2dc 55%,#ffffff 80%)"></div>
  <div class="product-name">Product - 1</div><div class="product-desc">Lorem ipsum dolor sit amet</div>
</div>
<div class="product-card" style="left:360px">
  <div class="media" role="img" aria-label="Silver link watch" style="background:radial-gradient(ellipse 30% 60%,#9b9ea6 0%,#e3e4e8 60%,#ffffff 90%)"></div>
  <div class="product-name">Product - 2</div><div class="product-desc">Lorem ipsum dolor sit amet</div>
</div>
<div class="product-card" style="left:609px">
  <div class="media" role="img" aria-label="Thin rose gold diamond bangle" style="background:radial-gradient(ellipse 60% 30%,#e0a77b 0%,#f6e6d9 60%,#ffffff 90%)"></div>
  <div class="product-name">Product - 3</div><div class="product-desc">Lorem ipsum dolor sit amet</div>
</div>
<div class="product-card" style="left:856px">
  <div class="media" role="img" aria-label="White gold ring with dark red stone" style="background:radial-gradient(circle,#c2b6bd 0%,#eee9ec 55%,#ffffff 80%)"></div>
  <div class="product-name">Product - 4</div><div class="product-desc">Lorem ipsum dolor sit amet</div>
</div>

<section class="video-band" aria-label="Video"></section>
<h2 class="section-title script" style="top:2600px;color:var(--white)">Our Video</h2>
<div class="title-rule" style="top:2661px"></div>
<div class="video-frame">
  <div class="media" role="img" aria-label="Interior of the jewelry store with log walls and display cases" style="left:0;top:0;width:100%;height:100%;background:linear-gradient(180deg,#5a4a36 0%,#b07a3a 40%,#8e5a2a 70%,#3a2a1e 100%)"></div>
  <div class="play-ring"><svg width="40" height="44" viewBox="0 0 40 44"><path d="M6 2 38 22 6 42z" fill="#fff"/></svg></div>
  <div class="play-cta">Click To Play</div>
  <div class="video-controls">
    <svg width="40" height="26" viewBox="0 0 40 26"><rect width="40" height="26" rx="3" fill="#000"/><path d="M15 7l12 6-12 6z" fill="#fff"/></svg>
    <span class="video-time">01:58</span>
    <div class="video-track"></div>
    <svg width="40" height="12" viewBox="0 0 40 12"><rect x="0" y="8" width="2" height="4" fill="#5cf"/><rect x="4" y="6" width="2" height="6" fill="#5cf"/><rect x="8" y="4" width="2" height="8" fill="#5cf"/><rect x="12" y="2" width="2" height="10" fill="#fff"/><circle cx="24" cy="6" r="4" fill="#fff"/><path d="M32 1h7v7M32 11h7V4" stroke="#fff" stroke-width="1.5" fill="none"/></svg>
  </div>
</div>

<h2 class="section-title script" style="top:3150px">Client Testimonials</h2>
<div class="title-rule" style="top:3211px"></div>
<div class="media" role="img" aria-label="Large solitaire diamond engagement ring" style="left:430px;top:3258px;width:340px;height:432px;background:radial-gradient(ellipse 50% 38% at 50% 62%,#ffffff 78%,#c9ced8 84%,#eef0f4 92%,#ffffff 100%),radial-gradient(circle at 50% 12%,#dfe3ea 0%,#ffffff 60%)"></div>

<svg class="quote-mark" style="left:206px;top:3404px" viewBox="0 0 90 70"><path d="M4 68V38C4 16 16 4 36 2v14c-10 2-15 9-15 20h15v32zM52 68V38c0-22 12-34 32-36v14c-10 2-15 9-15 20h15v32z" fill="var(--teal)"/></svg>
<svg class="quote-mark" style="left:555px;top:3404px" viewBox="0 0 90 70"><path d="M4 68V38C4 16 16 4 36 2v14c-10 2-15 9-15 20h15v32zM52 68V38c0-22 12-34 32-36v14c-10 2-15 9-15 20h15v32z" fill="var(--teal)"/></svg>
<svg class="quote-mark" style="left:913px;top:3404px" viewBox="0 0 90 70"><path d="M4 68V38C4 16 16 4 36 2v14c-10 2-15 9-15 20h15v32zM52 68V38c0-22 12-34 32-36v14c-10 2-15 9-15 20h15v32z" fill="var(--teal)"/></svg>

<p class="quote-text" style="left:111px;top:3489px">Lorem ipsum dolor sit amet, consectetur adipiscing elit, sed do eiusmod tempor incididunt ut labore et dolore magna minim veniam, quis aliqua.</p>
<p class="quote-text" style="left:460px;top:3489px">We get all our jewelry from Marwick Jewelers. They have great hometown service, a beautiful selection and great prices!</p>
<p class="quote-text" style="left:818px;top:3489px">Lorem ipsum dolor sit amet, consectetur adipiscing elit, sed do eiusmod tempor incididunt ut labore et dolore magna minim veniam, quis aliqua.</p>
<div class="quote-name" style="left:111px;top:3608px">-Rachel</div>
<div class="quote-name" style="left:460px;top:3608px">-Rachel</div>
<div class="quote-name" style="left:818px;top:3608px">-Rachel</div>

<section class="contact-band" aria-label="Contact and footer"></section>

<div class="panel" style="left:134px;top:3776px;width:341px;height:505px">
  <h2 class="abs" style="left:32px;top:62px">Contact Information</h2>
  <div class="info-row" style="top:114px"><svg width="16" height="20" viewBox="0 0 24 30" fill="#fff"><path d="M12 0a11 11 0 0 0-11 11c0 8 11 19 11 19s11-11 11-19A11 11 0 0 0 12 0zm0 15a4 4 0 1 1 0-8 4 4 0 0 1 0 8z"/></svg>48 Elm St N, Ashford, MN 55990</div>
  <div class="info-row" style="top:150px"><svg width="18" height="18" viewBox="0 0 24 24" fill="#fff"><path d="M6.6 10.8a15 15 0 0 0 6.6 6.6l2.2-2.2a1 1 0 0 1 1-.25 11.4 11.4 0 0 0 3.6.57 1 1 0 0 1 1 1V20a1 1 0 0 1-1 1A17 17 0 0 1 3 4a1 1 0 0 1 1-1h3.5a1 1 0 0 1 1 1c0 1.25.2 2.45.57 3.57a1 1 0 0 1-.25 1z"/></svg>555-201-4830</div>
  <div class="info-row" style="top:186px"><svg width="20" height="16" viewBox="0 0 24 20" fill="#fff"><path d="M2 6c0-3 5-5 10-5s10 2 10 5v2h-5V6H7v2H2zM5 10h14l2 9H3z"/></svg>888-555-0147</div>
  <h2 class="abs" style="left:32px;top:232px">Store Hours</h2>
  <div class="toggle" style="left:278px;top:246px"></div>
  <div class="hours-row" style="top:306px"><span>Monday - Friday</span><span>9am – 5:30pm</span></div>
  <div class="hours-row" style="top:363px"><span>Saturday</span><span>10am – 2pm</span></div>
  <div class="hours-row" style="top:423px;border-bottom:none"><span>Sunday</span><span>Closed</span></div>
</div>

<div class="media" role="img" aria-label="Street map showing the store location in downtown Ashford" style="left:475px;top:3776px;width:277px;height:505px;background:linear-gradient(160deg,#eef0ec 0%,#e6e9e3 50%,#dfe5ea 100%)"></div>

<div class="panel" style="left:752px;top:3776px;width:314px;height:505px">
  <h2 class="abs" style="left:36px;top:20px">Get In Touch</h2>
  <div class="field" style="top:74px">Name</div>
  <div class="field" style="top:123px">Phone</div>
  <div class="field" style="top:171px">Email</div>
  <div class="field" style="top:220px">How can we help you? <svg width="12" height="8" viewBox="0 0 12 8"><path d="M1 1l5 5 5-5" stroke="#8b909c" stroke-width="1.5" fill="none"/></svg></div>
  <div class="field" style="top:268px">How did you hear about us? <svg width="12" height="8" viewBox="0 0 12 8"><path d="M1 1l5 5 5-5" stroke="#8b909c" stroke-width="1.5" fill="none"/></svg></div>
  <div class="field area" style="top:316px">Meeage</div>
  <div class="btn-submit">SUBMIT NOW</div>
</div>

<div class="brand" style="left:520px;top:4345px;font-size:36px;color:var(--white)"><span class="brand-dot" style="background:var(--white)"></span>Marwick</div>

<nav class="footer-nav">
  <span>Company</span><span>Custom Jewelery Services</span><span>Jewelery Repair Services</span><span>Resources</span><span>Showcase</span><span>Gallery</span><span>Engraving &amp; Trophies</span><span>Gift Ideas</span>
</nav>
<div class="socials" aria-label="Social links"><span></span><span></span><span></span></div>
<p class="copyright">Copyrights © Marwick Jewelers 2022 | Allrights Reserved</p>

</body>
</html>
```